cryotherapy business . Whole Body Cryotherapy, Localised Cryotherapy, Cryofacials

Need home page plus services, about, pricing, online booking, contact and blog page

I want something slick, hip and professional. Our studio colours are duck egg blue, white and grey

I would also like a social media scroll at the bottom of every page

I will upload some web designs that I like the look of

Target Market(s)

Men and Women 25-45

Industry/Entity Type

Health And Wellness

Coding

Coded - Design and coding required

Number of Pages Required

5+ page

Font styles to use
Serif
Sans Serif

Requirements
Must have
• Must be eye catching and easy to navigate
Nice to have
• animation
Should not have
• Not sure what the site should not have. I am fairly open to ideas as this is a brand new business.

```html
<!DOCTYPE html>
<html lang="en">
<head>
<meta charset="utf-8">
<title>Frostline – Integrated Cryotherapy</title>
<link rel="stylesheet" href="https://fonts.googleapis.com/css2?family=Raleway:wght@200;300;400;600;700&family=Open+Sans:wght@400;600&display=swap">
<style>
:root{
  --navy:#0b2a8c;
  --blue:#1646c4;
  --sky:#5f8fe6;
  --teal:#2ec4a8;
  --teal-dark:#1fae94;
  --mint:#e8faf6;
  --ink:#2f3a44;
  --grey:#6f7780;
  --light:#f3f4f6;
  --footer:#232527;
  --footer-dark:#1a1b1d;
  --white:#ffffff;
}
*{box-sizing:border-box;margin:0;padding:0}
html,body{width:1200px;height:4248px;overflow:hidden}
body{font-family:"Open Sans",Arial,sans-serif;color:var(--ink);background:var(--white);position:relative}
.section-title{font-family:"Raleway",Arial,sans-serif;font-weight:600;font-size:40px;text-align:center;letter-spacing:1px;color:var(--ink)}
.section-title::after{content:"";display:block;width:60px;height:3px;background:var(--teal);margin:14px auto 0}

/* hero */
.hero{position:absolute;top:0;left:0;width:1200px;height:732px;background:linear-gradient(180deg,#0a2486 0%,#1747c8 45%,#3d73dc 70%,#dfe9f8 100%);overflow:hidden}
.hero-mist{position:absolute;left:0;right:0;bottom:0;height:330px;background:radial-gradient(ellipse at 30% 80%,rgba(255,255,255,.95),rgba(255,255,255,0) 60%),radial-gradient(ellipse at 75% 85%,rgba(255,255,255,.9),rgba(255,255,255,0) 55%),linear-gradient(180deg,rgba(255,255,255,0),#fff)}
.nav{position:absolute;top:0;left:0;right:0;height:100px;display:flex;align-items:center;justify-content:space-between;padding:0 112px}
.brand{font-family:"Raleway",sans-serif;font-weight:300;font-size:34px;letter-spacing:5px;color:var(--white)}
.nav-links{display:flex;gap:36px;list-style:none}
.nav-links li{font-family:"Raleway",sans-serif;font-weight:600;font-size:13px;color:var(--white);letter-spacing:.5px}
.hero-copy{position:absolute;top:226px;left:0;right:0;text-align:center;color:var(--white)}
.hero-kicker{font-family:"Raleway",sans-serif;font-size:17px;letter-spacing:5px;font-weight:400}
.hero-title{font-family:"Raleway",sans-serif;font-weight:200;font-size:170px;line-height:1;letter-spacing:22px;margin:14px 0 18px}
.hero-sub{font-family:"Raleway",sans-serif;font-size:18px;letter-spacing:6px}

/* about */
.about{position:absolute;top:732px;left:0;width:1200px;height:688px;background:var(--white)}
.about-photo{position:absolute}
.about-photo.towel{left:112px;top:196px;width:464px;height:276px;background:linear-gradient(135deg,#e9dccb,#b9a48b 55%,#f1f1f3)}
.about-photo.chamber{left:292px;top:292px;width:352px;height:316px;background:linear-gradient(135deg,#dfe4ea,#8e97a6 55%,#2e3644);border:6px solid var(--white)}
.about-text{position:absolute;left:692px;top:250px;width:470px}
.about-text h2{font-family:"Raleway",sans-serif;font-weight:700;font-size:30px;color:var(--teal);margin-bottom:26px}
.about-text p{font-size:13px;line-height:24px;color:var(--grey);margin-bottom:18px;text-align:justify}
.btn-outline{display:inline-block;border:2px solid var(--teal);color:var(--teal-dark);font-family:"Raleway",sans-serif;font-weight:600;font-size:13px;padding:11px 20px;margin-top:6px}

/* services */
.services{position:absolute;top:1420px;left:0;width:1200px;height:760px;background:var(--mint)}
.services .section-title{margin-top:40px}
.service-cards{display:flex;gap:24px;justify-content:center;margin-top:50px}
.service-card{width:316px;height:560px;background:var(--teal);color:var(--white)}
.service-photo{height:232px;background:linear-gradient(135deg,#1d4fc4,#8eb2ee)}
.service-card:nth-child(2) .service-photo{background:linear-gradient(135deg,#2c3440,#c9d3df)}
.service-card:nth-child(3) .service-photo{background:linear-gradient(135deg,#e5d6cc,#5fbfae)}
.service-body{padding:22px 26px}
.service-body h3{font-family:"Raleway",sans-serif;font-weight:700;font-size:17px;text-align:center}
.service-body .tagline{font-size:11px;text-align:center;opacity:.85;margin:6px 0 22px}
.price-row{display:flex;justify-content:space-between;font-size:13px;padding:10px 0;border-bottom:1px solid rgba(255,255,255,.35)}
.btn-wrap{text-align:center}
.btn-pill{display:inline-block;margin-top:30px;border:2px solid var(--white);border-radius:24px;padding:9px 24px;font-family:"Raleway",sans-serif;font-weight:600;font-size:14px}

/* media */
.media{position:absolute;top:2180px;left:0;width:1200px;height:752px}
.media .section-title{margin-top:66px}
.video{position:absolute;left:300px;top:140px;width:600px;height:552px;background:radial-gradient(ellipse at 50% 40%,#c07a3c,#6b3b18 60%,#2b170a)}
.play{position:absolute;left:260px;top:236px}

/* reviews */
.reviews{position:absolute;top:2932px;left:0;width:1200px;height:348px;background:linear-gradient(90deg,#46c6b0,#7ad8c7 50%,#46c6b0)}
.reviews .section-title{margin-top:40px;color:var(--white)}
.reviews .section-title::after{background:var(--white)}
.review{width:640px;margin:26px auto 0;text-align:center;color:var(--white);font-size:13px;line-height:24px;position:relative}
.review-author{margin-top:14px;font-family:"Raleway",sans-serif;font-weight:700;font-size:13px;letter-spacing:1px}
.stars{font-size:14px;letter-spacing:3px}
.quote{position:absolute;font-family:"Raleway",serif;font-size:54px;line-height:1;opacity:.8}
.arrow{position:absolute;top:120px}

/* blog */
.blog{position:absolute;top:3280px;left:0;width:1200px;height:588px;background:var(--light)}
.blog .section-title{margin-top:44px}
.blog-cards{display:flex;gap:28px;justify-content:center;margin-top:40px}
.blog-card{width:308px;height:392px;background:var(--white)}
.blog-photo{height:232px;background:linear-gradient(135deg,#1c2a70,#6a84c8)}
.blog-card:nth-child(2) .blog-photo{background:linear-gradient(135deg,#9aa6b4,#3d4855)}
.blog-card:nth-child(3) .blog-photo{background:linear-gradient(135deg,#2050c8,#c9d4e4)}
.blog-body{padding:18px 22px}
.blog-meta{font-size:11px;color:var(--teal-dark);font-weight:600;margin-bottom:10px}
.blog-body p{font-size:14px;line-height:21px;color:var(--ink)}

/* footer */
.footer{position:absolute;top:3868px;left:0;width:1200px;height:380px;background:var(--footer);color:#cfd3d6}
.footer-cols{position:absolute;top:58px;left:112px;display:flex}
.footer-col h4{font-family:"Raleway",sans-serif;font-weight:700;font-size:15px;color:var(--white);margin-bottom:20px;letter-spacing:.5px}
.footer-col.contact{width:260px}
.footer-col.links{width:200px}
.footer-col.hours{width:270px}
.footer-col li{list-style:none;font-size:12px;line-height:26px;display:flex;align-items:center;gap:10px}
.footer-brand{position:absolute;left:830px;top:96px;width:260px;text-align:center}
.footer-brand .brand{font-size:30px}
.socials{display:flex;gap:12px;justify-content:center;margin-top:16px}
.socials span{width:30px;height:30px;border:2px solid #cfd3d6;border-radius:50%}
.copyright{position:absolute;left:0;right:0;bottom:0;height:56px;background:var(--footer-dark);text-align:center;line-height:56px;font-size:12px;color:var(--white)}
</style>
</head>
<body>

<header class="hero">
  <div class="hero-mist" role="img" aria-label="Cold mist rolling across the bottom of the banner"></div>
  <nav class="nav">
    <div class="brand">FROSTLINE</div>
    <ul class="nav-links">
      <li>HOME</li><li>SERVICES</li><li>ABOUT</li><li>PRICING</li><li>ONLINE BOOKING</li><li>CONTACT &amp; BLOG</li>
    </ul>
  </nav>
  <div class="hero-copy">
    <div class="hero-kicker">THE POWER OF</div>
    <h1 class="hero-title">COLD</h1>
    <div class="hero-sub">INTEGRATED CRYOTHERAPY</div>
  </div>
</header>

<section class="about">
  <div class="about-photo towel" role="img" aria-label="Client wrapped in a white towel before a session"></div>
  <div class="about-photo chamber" role="img" aria-label="Client in robe beside a cryotherapy chamber with a therapist"></div>
  <div class="about-text">
    <h2>WHAT IS CRYOTHERAPY?</h2>
    <p>Originally invented by doctors as a powerful anti-inflammatory tool, cryotherapy is a quick, noninvasive process that exposes your body to extreme cold of up to -110°F. The sudden drop in temperature increases circulation and pumps oxygenated and nutrient enriched blood back into the bloodstream, reducing pain and inflammation and alleviating sore muscles. It's also known to release feel good endorphins that help improve sleep, reduce stress, and elevate your mood.</p>
    <p>At Frostline, we believe that cryotherapy is one point on the wellness wheel. Our focus is to integrate cryotherapy into your routine as part of your health &amp; wellness regimen.</p>
    <span class="btn-outline">READ MORE</span>
  </div>
</section>

<section class="services">
  <h2 class="section-title">OUR SERVICES</h2>
  <div class="service-cards">
    <article class="service-card">
      <div class="service-photo" role="img" aria-label="Client smiling inside a whole body cryo chamber"></div>
      <div class="service-body">
        <h3>WHOLE BODY CRYOTHERAPY</h3>
        <div class="tagline">Full body cold exposure in three minutes</div>
        <div class="price-row"><span>Single</span><span>$65</span></div>
        <div class="price-row"><span>10 Pack</span><span>$550</span></div>
        <div class="price-row"><span>20 Pack</span><span>$720</span></div>
        <div class="price-row"><span>Monthly*</span><span>$450</span></div>
        <div class="btn-wrap"><span class="btn-pill">Buy Now!</span></div>
      </div>
    </article>
    <article class="service-card">
      <div class="service-photo" role="img" aria-label="Cold vapour applied to a client's leg"></div>
      <div class="service-body">
        <h3>LOCAL CRYOTHERAPY</h3>
        <div class="tagline">Reduce pain and swelling in targeted areas</div>
        <div class="price-row"><span>Single</span><span>$30</span></div>
        <div class="price-row"><span>10 Pack</span><span>$180</span></div>
        <div class="price-row"><span>20 Pack</span><span>$720</span></div>
        <div class="price-row"><span>Monthly*</span><span>$450</span></div>
        <div class="btn-wrap"><span class="btn-pill">Buy Now!</span></div>
      </div>
    </article>
    <article class="service-card">
      <div class="service-photo" role="img" aria-label="Cryo facial being applied to a relaxed client"></div>
      <div class="service-body">
        <h3>CRYO FACIAL</h3>
        <div class="tagline">Tighten, tone and refresh your skin</div>
        <div class="price-row"><span>Single</span><span>$65</span></div>
        <div class="price-row"><span>10 Pack</span><span>$550</span></div>
        <div class="price-row"><span>20 Pack</span><span>$720</span></div>
        <div class="price-row"><span>Monthly*</span><span>$450</span></div>
        <div class="btn-wrap"><span class="btn-pill">Buy Now!</span></div>
      </div>
    </article>
  </div>
</section>

<section class="media">
  <h2 class="section-title">OUR MEDIA</h2>
  <div class="video" role="img" aria-label="Video still of a client inside a cryo chamber surrounded by vapour">
    <svg class="play" width="80" height="80" viewBox="0 0 80 80" aria-hidden="true">
      <circle cx="40" cy="40" r="36" fill="none" stroke="#fff" stroke-width="3"/>
      <path d="M32 25 L56 40 L32 55 Z" fill="none" stroke="#fff" stroke-width="3" stroke-linejoin="round"/>
    </svg>
  </div>
</section>

<section class="reviews">
  <h2 class="section-title">OUR REVIEWS</h2>
  <svg class="arrow" style="left:150px" width="20" height="36" viewBox="0 0 20 36" aria-hidden="true"><path d="M17 2 L3 18 L17 34" fill="none" stroke="#fff" stroke-width="2"/></svg>
  <svg class="arrow" style="right:150px" width="20" height="36" viewBox="0 0 20 36" aria-hidden="true"><path d="M3 2 L17 18 L3 34" fill="none" stroke="#fff" stroke-width="2"/></svg>
  <div class="review">
    <span class="quote" style="left:-46px;top:-6px">“</span>
    <p>I came in with sore knees after months of training and left feeling lighter than I have in years. The team explained every step, the studio is calm and spotless, and three minutes in the chamber now sets me up for the whole week. Highly recommend.</p>
    <span class="quote" style="right:-46px;bottom:20px">”</span>
    <div class="review-author">DANIEL K.</div>
    <div class="stars">★★★★★</div>
  </div>
</section>

<section class="blog">
  <h2 class="section-title">LATEST BLOG</h2>
  <div class="blog-cards">
    <article class="blog-card">
      <div class="blog-photo" role="img" aria-label="Group of clients celebrating at a studio event"></div>
      <div class="blog-body">
        <div class="blog-meta">by Anna Reed | Jan 03, 2019</div>
        <p>Five reasons our members book a morning session before work each week…</p>
      </div>
    </article>
    <article class="blog-card">
      <div class="blog-photo" role="img" aria-label="Cryotherapy chamber inside the studio"></div>
      <div class="blog-body">
        <div class="blog-meta">by Anna Reed | Jan 03, 2019</div>
        <p>What really happens to your body during three minutes at extreme cold…</p>
      </div>
    </article>
    <article class="blog-card">
      <div class="blog-photo" role="img" aria-label="Client stepping into a vapour filled chamber"></div>
      <div class="blog-body">
        <div class="blog-meta">by Anna Reed | Jan 03, 2019</div>
        <p>How athletes use cold therapy to recover faster between hard sessions…</p>
      </div>
    </article>
  </div>
</section>

<footer class="footer">
  <div class="footer-cols">
    <div class="footer-col contact">
      <h4>CONTACT US</h4>
      <ul>
        <li><svg width="12" height="14" viewBox="0 0 12 14" aria-hidden="true"><path d="M6 1a4.5 4.5 0 0 0-4.5 4.5C1.5 9 6 13 6 13s4.5-4 4.5-7.5A4.5 4.5 0 0 0 6 1z" fill="#cfd3d6"/><circle cx="6" cy="5.5" r="1.6" fill="#232527"/></svg>14 Harbour Lane, Northgate</li>
        <li><svg width="12" height="12" viewBox="0 0 12 12" aria-hidden="true"><path d="M2.5 1l2 2.5-1.2 1.2a7 7 0 0 0 4 4L8.5 7.5 11 9.5 9.8 11C5 11 1 7 1 2.2z" fill="#cfd3d6"/></svg>(555) 014-2290</li>
        <li><svg width="12" height="10" viewBox="0 0 12 10" aria-hidden="true"><rect x="0.5" y="0.5" width="11" height="9" fill="#cfd3d6"/><path d="M.5 .5 6 5.5 11.5 .5" fill="none" stroke="#232527"/></svg>hello@frostline-studio.com</li>
      </ul>
    </div>
    <div class="footer-col links">
      <h4>QUICK LINKS</h4>
      <ul>
        <li>▸ Home</li><li>▸ Services</li><li>▸ About</li><li>▸ Pricing</li><li>▸ Online Booking</li><li>▸ Contact &amp; Blog</li>
      </ul>
    </div>
    <div class="footer-col hours">
      <h4>OPENING HOURS</h4>
      <ul>
        <li>▸ Mon – Fri 9:00 am – 8:00 pm</li><li>▸ Saturday 9:00 am – 3:00 pm</li><li>▸ Sunday Closed</li>
      </ul>
    </div>
  </div>
  <div class="footer-brand">
    <div class="brand">FROSTLINE</div>
    <div class="socials" aria-label="Social media links"><span></span><span></span><span></span><span></span></div>
  </div>
  <div class="copyright">Copyrights © 2019 Frostline All Rights Reserved</div>
</footer>

</body>
</html>
```